Golden Coat All-Purpose Breading Bag Design

Our client, Halvern Food Products, is looking to re-design the packaging for their product, Pellham's Golden Coat. Goldn Coat is an all-purpose food breading mix.

Halvern Foods has a registered trademark for this product, but they have not been using it for this particular 10 pound bag. They want to get the trademark onto the bag and also give the bag an updated look. They would like to continue to use the same red and blue colors. This 10 pound bag is not available on store shelves; it is sold to food service distributors who sell to restaurants.

All of the copy on the existing bag is still relevant, so we will want to incoprporate it into the bag design. Once these bags are filled with product, the tops get folded over about 1 inch and then sewn shut with thread.

Eventually, we will need the design applied to the Bag Template file attached, but that isn't important until a design is selected.

Target Market(s)

Restaurants

Industry/Entity Type

Food Manufacturing

Colors
0054AA
0677BA
7BADD7
CADEEF
E8F1F8
EB3D1F
EC4F4E
F09395
F8D3D4
FCEDEE

Requirements
Must have
• Trademark introduced to the design

```html
<!DOCTYPE html>
<html lang="en">
<head>
<meta charset="utf-8">
<title>Pellham's Golden Coat – 10 lb Bag Front</title>
<link rel="stylesheet" href="https://fonts.googleapis.com/css2?family=Barlow+Condensed:ital,wght@0,600;0,700;0,800;1,600;1,700&family=Montserrat:wght@600;700&display=swap">
<style>
  :root {
    --navy: #22397f;
    --red: #cf2027;
    --pill: #5c6fa8;
    --white: #ffffff;
    --paper: #ffffff;
    --stage: #f4f4f4;
  }
  * { box-sizing: border-box; margin: 0; padding: 0; }
  html, body { width: 1200px; height: 667px; overflow: hidden; background: var(--stage); }
  .canvas { position: relative; width: 1200px; height: 667px; }
  .bag-front {
    position: absolute; left: 396px; top: 0; width: 408px; height: 667px;
    background: var(--paper);
  }
  .bag-shapes { position: absolute; inset: 0; }
  .tagline {
    position: absolute; left: 90px; top: 126px; width: 230px;
    font-family: "Barlow Condensed", sans-serif; font-style: italic; font-weight: 700;
    font-size: 13px; line-height: 14px; color: var(--navy); letter-spacing: .2px;
    text-align: center; transform: rotate(-6deg);
  }
  .tagline .accent { color: var(--red); border-bottom: 1.5px solid var(--red); }
  .brand-name {
    position: absolute; left: 60px; top: 250px; width: 290px;
    font-family: "Barlow Condensed", sans-serif; font-weight: 800;
    color: var(--white); text-align: center; text-transform: uppercase;
  }
  .brand-name .maker { display: block; font-size: 22px; line-height: 24px; letter-spacing: 1px; }
  .brand-name .product { display: block; font-size: 50px; line-height: 52px; letter-spacing: .5px; white-space: nowrap; }
  .brand-name .trademark { font-size: 18px; vertical-align: 24px; }
  .descriptor {
    position: absolute; left: 94px; top: 340px; width: 220px;
    font-family: "Montserrat", sans-serif; font-weight: 700; font-size: 11px;
    line-height: 13px; color: var(--white); text-align: center; letter-spacing: .8px;
  }
  .claim {
    position: absolute; left: 115px; top: 406px; width: 182px; height: 20px;
    background: var(--pill); border-radius: 3px;
    font-family: "Barlow Condensed", sans-serif; font-weight: 700; font-size: 15px;
    line-height: 20px; color: var(--white); text-align: center; letter-spacing: .3px;
  }
  .cook-note {
    position: absolute; left: 80px; top: 430px; width: 252px;
    font-family: "Barlow Condensed", sans-serif; font-style: italic; font-weight: 600;
    font-size: 9.5px; line-height: 11.5px; color: var(--white); text-align: center;
  }
  .divider {
    position: absolute; left: 142px; top: 462px; width: 127px; height: 1px;
    background: var(--white); opacity: .85;
  }
  .ingredients {
    position: absolute; left: 100px; top: 474px; width: 212px;
    font-family: "Montserrat", sans-serif; font-weight: 700; font-size: 6.6px;
    line-height: 11.6px; color: var(--white); text-align: center; letter-spacing: .7px;
  }
  .net-weight {
    position: absolute; left: 0; top: 561px; width: 408px;
    font-family: "Montserrat", sans-serif; font-weight: 700; font-size: 10px;
    color: var(--navy); text-align: center; letter-spacing: 1px;
  }
</style>
</head>
<body>
<main class="canvas">
  <section class="bag-front">
    <svg class="bag-shapes" width="408" height="667" viewBox="0 0 408 667" aria-hidden="true">
      <rect class="lower-band" x="34" y="342" width="337" height="210" fill="var(--navy)"/>
      <path class="banner-edge" d="M49 234 L353 222 L336 383 L80 402 Z" fill="var(--white)"/>
      <path class="banner" d="M52 238 L350 227 L334 380 L81 398 Z" fill="var(--red)"/>
    </svg>

    <p class="tagline">CHICKEN FRIED THE GOLDEN COAT WAY<br>IS FRIED CHICKEN <span class="accent">THE RIGHT WAY.</span></p>

    <h1 class="brand-name"><span class="maker">Pellham's</span><span class="product">Golden Coat<span class="trademark">®</span></span></h1>

    <p class="descriptor">THE ALL PURPOSE BREADING</p>

    <p class="claim">SEALS JUICE IN - GREASE OUT</p>
    <p class="cook-note">COOKS TWO-POUND CHICKEN WELL DONE<br>IN 10 MINUTES (DEEP FAT).</p>
    <div class="divider"></div>
    <p class="ingredients">INGREDIENTS: FLOUR, SALT, NON-FAT MILK<br>SOLIDS, EGG YOLK, BAKING POWDER,<br>CORN STARCH, SUGAR AND PEPPER.</p>

    <p class="net-weight">NET WT. 10 LBS.</p>
  </section>
</main>
</body>
</html>
```